CBD AgriBusiness Verdant Trophy Business Card

We are HiTec producer of medical cannabis CBD Switzerland of high quality. Our website is alpinleaf.net, we will also revisit it graphically, the winner of this contest will be the graphic designer chosen for the new design of the website. We stand out by the skill of the team, many of our engineers we win cup cannabis. I join the current map to take as an example but to revisit completely: deletion of surname and first name, modification of funds (front / back), reorganization of text info, highlighting the address of the website. three characteristics define the business card: Professional, Class, refined. The business card must be optimized for soft-touch and selective varnish printing.

Target Market(s)

Customers and Suppliers

Industry/Entity Type

Agribusiness

Contact Information for Business Card

Logo, Tél / Whatsapp, mail, url du site : alpinleaf.net

Font styles to use
Sans Serif

Requirements
Must have
• Logo of alpinleaf.net
Nice to have
• a design that stands out well on the selective varnish
Should not have
• Last name and first name

```html
<!DOCTYPE html>
<html lang="en">
<head>
<meta charset="utf-8">
<title>AlpinLeaf Business Card</title>
<link href="https://fonts.googleapis.com/css2?family=Montserrat:wght@300;400;700;800&display=swap" rel="stylesheet">
<style>
  :root {
    --canvas-bg: #2b2d2d;
    --card-bg: #0d1111;
    --card-bg-deep: #070909;
    --leaf-light: #6f8a3a;
    --leaf-mid: #3c5220;
    --leaf-dark: #14200c;
    --brand-green: #6cc04a;
    --text-white: #f2f2f2;
    --text-soft: #d8dcd8;
  }
  * { margin: 0; padding: 0; box-sizing: border-box; }
  html, body {
    width: 1200px; height: 960px; overflow: hidden;
    background: var(--canvas-bg);
    font-family: "Montserrat", sans-serif;
  }
  .canvas { position: relative; width: 1200px; height: 960px; }

  .card {
    position: absolute; left: 220px; width: 760px; height: 434px;
    background: linear-gradient(160deg, var(--card-bg) 0%, var(--card-bg-deep) 100%);
    overflow: hidden;
    box-shadow: 0 10px 30px rgba(0,0,0,.45);
  }
  .card--contact { top: 36px; }
  .card--brand { top: 490px; }

  .foliage { position: absolute; }
  .foliage--contact-right {
    right: -60px; top: -60px; width: 460px; height: 500px;
    background: radial-gradient(ellipse at 65% 40%, var(--leaf-light) 0%, var(--leaf-mid) 35%, var(--leaf-dark) 60%, transparent 75%);
  }
  .foliage--brand-left {
    left: -80px; top: -40px; width: 330px; height: 520px;
    background: radial-gradient(ellipse at 30% 50%, var(--leaf-light) 0%, var(--leaf-mid) 30%, var(--leaf-dark) 58%, transparent 74%);
  }
  .foliage--brand-right {
    right: -70px; top: 60px; width: 340px; height: 440px;
    background: radial-gradient(ellipse at 65% 50%, var(--leaf-light) 0%, var(--leaf-mid) 32%, var(--leaf-dark) 58%, transparent 74%);
  }

  .brand-mark {
    position: absolute; display: flex; align-items: center; gap: 14px;
  }
  .brand-mark__square {
    width: 40px; height: 40px; background: var(--brand-green);
  }
  .brand-mark__name {
    font-weight: 800; color: var(--text-white); letter-spacing: -1px; line-height: 1;
  }
  .card--contact .brand-mark { left: 60px; top: 92px; }
  .card--contact .brand-mark__name { font-size: 62px; }

  .card--brand .brand-mark { left: 180px; top: 168px; }
  .card--brand .brand-mark__square { width: 46px; height: 46px; }
  .card--brand .brand-mark__name { font-size: 72px; }

  .contact-list {
    position: absolute; left: 118px; top: 190px; list-style: none;
  }
  .contact-list li {
    display: flex; align-items: center; gap: 14px;
    height: 42px; font-size: 20px; font-weight: 400; color: var(--text-soft);
  }
  .contact-icon { width: 28px; height: 28px; flex: none; }

  .contact-list .contact-website {
    margin-top: 14px; padding-top: 14px; height: 56px;
    border-top: 1px solid var(--brand-green);
    font-size: 26px; font-weight: 700; color: var(--brand-green);
  }

  .tagline {
    position: absolute; left: 260px; top: 256px;
    font-size: 22px; font-weight: 400; letter-spacing: 2px; color: var(--text-soft);
  }
</style>
</head>
<body>
<main class="canvas">

  <section class="card card--contact">
    <div class="foliage foliage--contact-right" role="img" aria-label="Photograph of green cannabis leaves in the top right corner"></div>
    <div class="brand-mark">
      <span class="brand-mark__square"></span>
      <span class="brand-mark__name">AlpinLeaf</span>
    </div>
    <ul class="contact-list">
      <li>
        <svg class="contact-icon" viewBox="0 0 28 28"><circle cx="14" cy="14" r="12" fill="none" stroke="var(--brand-green)" stroke-width="2"/><circle cx="14" cy="14" r="5" fill="var(--brand-green)"/></svg>
        555-014-2100
      </li>
      <li>
        <svg class="contact-icon" viewBox="0 0 28 28"><circle cx="14" cy="14" r="12" fill="none" stroke="var(--brand-green)" stroke-width="2"/><path d="M9.5 8.5 l3 0 l1 3.5 -1.8 1.3 a8 8 0 0 0 3.5 3.5 l1.3 -1.8 3.5 1 0 3 a1.5 1.5 0 0 1 -1.5 1.3 A10 10 0 0 1 8.2 10 a1.5 1.5 0 0 1 1.3 -1.5z" fill="var(--brand-green)"/></svg>
        555-014-2100
      </li>
      <li>
        <svg class="contact-icon" viewBox="0 0 28 28"><circle cx="14" cy="14" r="12" fill="none" stroke="var(--brand-green)" stroke-width="2"/><rect x="8" y="9.5" width="12" height="9" fill="var(--brand-green)"/><path d="M8 9.5 l6 5 6 -5" fill="none" stroke="var(--card-bg)" stroke-width="1.4"/></svg>
        hello@alpinleaf.net
      </li>
      <li class="contact-website">
        <svg class="contact-icon" viewBox="0 0 28 28"><circle cx="14" cy="14" r="12" fill="none" stroke="var(--brand-green)" stroke-width="2"/><circle cx="14" cy="14" r="6.5" fill="none" stroke="var(--brand-green)" stroke-width="1.6"/><ellipse cx="14" cy="14" rx="2.8" ry="6.5" fill="none" stroke="var(--brand-green)" stroke-width="1.4"/><path d="M7.5 14 h13" stroke="var(--brand-green)" stroke-width="1.4"/></svg>
        www.alpinleaf.net
      </li>
    </ul>
  </section>

  <section class="card card--brand">
    <div class="foliage foliage--brand-left" role="img" aria-label="Photograph of cannabis leaves along the left edge"></div>
    <div class="foliage foliage--brand-right" role="img" aria-label="Photograph of cannabis leaves in the lower right corner"></div>
    <div class="brand-mark">
      <span class="brand-mark__square"></span>
      <span class="brand-mark__name">AlpinLeaf</span>
    </div>
    <p class="tagline">ALPINE HEMP COLLECTIVE</p>
  </section>

</main>
</body>
</html>
```